Medical Practice and Business Coaching Website Design

I need a professional website designed for a medical business, TQP Medical.
The website will be hosted on Vorluna (similar design functionality as ZEPT).

About the website:
Pages for the website:
- Home page (a brief overview of the company with a section for "Ultrasound Clinics" and "Coaching and Courses" that link to these pages with all the info and packages for these sections)
- About Us (section for company info and info about Delphine Ashcombe, founder and business coach)
- Ultrasound Clinics (all the info about ultrasound, our packages, links to book, gallery of 3D/4D images, FAQs, social media links)
- Coaching and Courses (All of our coaching package info, course info with a waiting list sign up, section for free business download resources, social media links, blog posts)
- Contact Us (info for our harrowgate ultrasound location and bookings with a map, contact form, email and phone details)

Pages that are also needed but not visible in the top menu:
- Blog Page
- Waiting List Page x2 (Dubbo pop-up 3D clinic, Online Course)
- Thanks for subscribing page

We have a company logo and a logo for both the ultrasound clinics and the Coaching sides of the business. They are attached as well as the HEX codes for the branding colours. Ideally the company areas of the site will be in the blue, purple and teal colours. The ultrasound clinics page will be mostly in the purple with the "clinics" logo featuring on the page.
The courses and coaching page will be dominant in the blue branding colours with accents of purple and teal. The courses logo will be somewhere on the page too.

About our company:
Our company has 2 separate businesses which will have their own pages on the website.
We have a medical imaging business which specialises in ultrasound. We have 3 locations/services:
- Harrowgate Ultrasound: open Fridays and the occasional saturday. Our main focus and where the focus on the clinical page needs to be.
- East Corrimbal Ultrasound: Currently closed, no re-opening date and unlikely to reopen.
- Pop-up clinics: most commonly occur in Dubbo. occasionally in Parkes. Dates for next pop-up will be announced in the future.

Our Harrowgate practice offers both diagnostic ultrasound (referral from doctor) for all areas of the body and 3d/4d pregnancy ultrasounds for entertainment purposes.
The content for the ultrasound clinics part of the website can be found on the current harrowgate ultrasound website: harrowgateultrasound.com.au
This website will be replaced by the new company site. All of the info on this site will end up on the clinics page of the new company website.

The second part of the company is a coaching and courses service for medical professionals who want to start or grow their business.
We currently have coaching packages for 1-on-1 online advice and guidance.

Coaching: all take place on Zoom and can be recorded for them to watch again after. Notes, documents and links that are discussed are provided after session

- FREE 15 minute session: discuss current business or business idea, if and how I can help and potential things they can do. One per client

- Single Coaching Session - 1hr with Delphine

- Silver coaching package: 1 x 1hr Coaching Call with Delphine
Unlimited Email with Delphine for 1 month
Access to our Private Facebook Group to network with other medical professionals and business owners

- Silver Coaching Package With Social Media Management:
As above with 1 month Social Media Management (15 posts, Facebook and Instagram)

- Gold coaching package: 2 x 1hr Coaching Calls with Delphine
Access to our Private Facebook

- Gold Coaching Package With Social Media Management:

- Business Sidekick Package: Unlimited Coaching Calls
Unlimited SMS
Unlimited Emails
Social Media Management (Facebook and Instagram, 1 post per day) Valued at over $700
Business Masterclass (something different each month...social media, medicare, website, branding, live events, etc)

Enrollment for our first course opens in May and clients can join the waitlist in the meantime.
Course is aimed at medical professionals who want to grow their patient numbers and create an online presence for their business.
Ideal for: small practices where the owner does everything, not necessarily familiar with marketing/social media/websites, goes to the very basics and steps through everything in getting a logo, branding, website, building social media pages, creating content.

Course name to come but it will be something like "helpful marketing in healthcare" or "the business of healthcare"

We will also have a blog on the website and a podcast (in the future).

I would like a testimonial on at least the clinics page and the coaching page. Here is one for each but I have more if need be:
Coaching: "I knew I wanted to start my own business but I had no idea where to begin. It would have been easy to abort my dreams of starting my own business had it not been for the direction and unwavering support of Delphine from TQP medical. Delphine dissected the process into manageable bit sized pieces for me and worked tirelessly behind the scenes ensuring everything was on track. Her friendly, warm and approachable manner
equated to more than her just being my business coach, she has now become a friend.
Thank you!!"

Ultrasound testimonial: "Amazing service! Best ultrasound experience I’ve had. Super friendly and informative staff. Great technology. If I didn’t live so far away I’d go to Harrowgate for all my ultrasounds!"

I would also like a section for a welcome video (yet to be recorded) on the home page, ultrasound clinics page and coaching/courses page.

I've attached the company logo and the sub-logos in different formats. There is also a head shot of Delphine for the about us page, an image of Delphine with a coaching client for the coaching page and multiple 3D ultrasound images for the gallery on the clinics page.

Target Market(s)

Mostly targeted at medical professionals. Pregnant women and anyone needing an ultrasound are the targets for the clinics page

Industry/Entity Type

Healthcare

Number of Pages Required

5+ page

Colors
0054AA
0677BA
7BADD7
CADEEF
E8F1F8
0094D4
00A9DD
6FCCEA
C7EBF8
E9F6FB
00AB8E
00BBA5
67D7C9
C6EFE9
E9F9F6
A7469A
B969AE
D3A5CF
EDDBEB
F8F0F9
6B429C
8869AF
B7A5CE
E3DAEB
F3F0F8

```html
<!DOCTYPE html>
<html lang="en">
<head>
<meta charset="utf-8">
<title>TQP Medical</title>
<link rel="stylesheet" href="https://fonts.googleapis.com/css2?family=Old+Standard+TT:wght@400;700&family=Roboto:wght@400;700&family=Merriweather:wght@300;400&family=Montserrat:wght@400&display=swap">
<style>
:root{
  --purple:#5a3591;
  --purple-deep:#4d3790;
  --teal:#23939b;
  --teal-btn:#1d8fa0;
  --ink:#2b2a33;
  --muted:#55535e;
  --grey-bg:#f3f3f3;
  --lilac-bg:#e4e2ef;
  --quote:#b9b6c2;
  --footer:#232325;
  --white:#ffffff;
}
*{box-sizing:border-box;margin:0;padding:0}
html,body{width:1200px;height:4736px;overflow:hidden}
body{position:relative;background:var(--white);font-family:"Merriweather",Georgia,serif;color:var(--ink)}
.abs{position:absolute}
.serif-head{font-family:"Old Standard TT",Georgia,serif;font-weight:700;color:var(--ink)}

/* header */
.site-header{position:absolute;left:0;top:0;width:1200px;height:88px;background:var(--white)}
.brand{position:absolute;left:73px;top:6px;display:flex;align-items:center;gap:12px}
.brand-dot{width:74px;height:74px;border-radius:50%;border:4px solid var(--purple)}
.brand-name{font-family:"Old Standard TT",Georgia,serif;font-size:19px;color:var(--purple);line-height:1.05;text-transform:uppercase;letter-spacing:1px}
.nav a{position:absolute;top:34px;font-family:"Old Standard TT",Georgia,serif;font-size:13.5px;color:var(--ink);text-decoration:none;white-space:nowrap}
.btn-book{position:absolute;left:891px;top:24px;width:125px;height:40px;background:var(--teal);color:var(--white);font-family:"Old Standard TT",Georgia,serif;font-size:12px;letter-spacing:1px;display:flex;align-items:center;justify-content:center}
.btn-contact{position:absolute;left:1022px;top:24px;width:127px;height:40px;border:2px solid var(--teal);color:var(--ink);font-family:"Old Standard TT",Georgia,serif;font-size:12px;letter-spacing:1px;display:flex;align-items:center;justify-content:center}

/* buttons */
.btn-learn{position:absolute;height:46px;border-radius:23px;background:linear-gradient(90deg,var(--purple-deep),var(--teal-btn));color:var(--white);font-family:"Roboto",Arial,sans-serif;font-weight:700;font-size:15px;display:flex;align-items:center;justify-content:center;gap:8px;box-shadow:0 3px 6px rgba(0,0,0,.2)}
.btn-learn svg{width:15px;height:15px}

/* hero */
.hero{position:absolute;left:0;top:88px;width:1200px;height:597px;background:linear-gradient(100deg,#7a3a34 0%,#b9685a 25%,#c9c2b8 45%,#e7e4e2 70%,#9d9aa1 100%)}
.hero-title{position:absolute;left:112px;top:180px;font-family:"Old Standard TT",Georgia,serif;font-weight:700;font-size:64px;color:var(--white);letter-spacing:1px}
.play{position:absolute;left:803px;top:277px;display:flex;align-items:center;gap:10px;font-family:"Old Standard TT",Georgia,serif;font-size:14px;color:var(--white);text-decoration:underline}
.play-dot{width:44px;height:44px;border-radius:50%;background:var(--white);display:flex;align-items:center;justify-content:center}

/* clinics */
.clinic-ring{position:absolute;left:112px;top:770px;width:486px;height:486px;border-radius:50%;border:14px solid var(--purple)}
.clinic-ring-inner{position:absolute;left:158px;top:816px;width:394px;height:394px;border-radius:50%;border:14px solid var(--teal)}
.clinic-photo{position:absolute;left:175px;top:833px;width:360px;height:360px;border-radius:50%;background:linear-gradient(120deg,#c4cbd3,#d9c3b9 40%,#a85a4d 70%,#6b7580)}
.section-title{font-family:"Old Standard TT",Georgia,serif;font-weight:700;font-size:38px;color:#4a4a55;letter-spacing:.5px}
.section-title span{color:var(--purple)}
.clinic-copy{position:absolute;left:660px;top:903px;width:428px;font-family:"Roboto",Arial,sans-serif;font-size:14px;line-height:26.6px;color:var(--muted);text-align:justify}
.clinic-copy p+p{margin-top:7px}

/* coaching */
.coaching{position:absolute;left:0;top:1327px;width:1200px;height:737px;background:linear-gradient(180deg,#5a3591 0%,#3b5b97 45%,#1f8f9a 100%)}
.coaching-photo{position:absolute;left:476px;top:83px;width:612px;height:569px;background:linear-gradient(135deg,#6d5443,#a88a72 40%,#9fb4d0 65%,#e6e1db)}
.coaching-card{position:absolute;left:116px;top:156px;width:467px;height:421px;background:rgba(245,245,250,.95);border-radius:6px;box-shadow:0 4px 16px rgba(0,0,0,.2)}
.coaching-card h2{position:absolute;left:0;width:100%;top:34px;padding-left:66px;font-family:"Old Standard TT",Georgia,serif;font-weight:400;font-size:27px;color:var(--ink);letter-spacing:1px}
.coaching-card p{position:absolute;left:44px;top:78px;width:356px;font-size:16px;line-height:25.7px;color:var(--muted);text-align:justify;text-align-last:right;font-weight:300}

/* video */
.welcome{position:absolute;left:0;top:2064px;width:1200px;height:689px;background:var(--grey-bg)}
.centered-title{position:absolute;left:0;width:1200px;text-align:center;font-family:"Old Standard TT",Georgia,serif;font-weight:700;font-size:23px;color:var(--ink);letter-spacing:1px}
.video{position:absolute;left:202px;top:156px;width:796px;height:437px;background:#000}
.video-frame{position:absolute;left:0;top:0;width:796px;height:410px;background:radial-gradient(ellipse 120px 190px at 400px 200px,#b47a52 0%,#6a3a22 55%,#000 100%)}
.video-bar{position:absolute;left:0;top:410px;width:796px;height:27px;background:#1fa090;display:flex;align-items:center;gap:10px;padding:0 12px;font-family:"Roboto",Arial,sans-serif;font-size:11px;color:var(--white)}
.video-track{flex:1;height:2px;background:rgba(255,255,255,.7)}

/* testimonial */
.quote-mark{position:absolute;left:150px;top:2885px;font-family:"Old Standard TT",Georgia,serif;font-weight:700;font-size:240px;line-height:1;color:var(--quote)}
.avatar{position:absolute;left:533px;top:2907px;width:132px;height:132px;border-radius:50%;background:linear-gradient(160deg,#d8e2ea,#7a5a4a 55%,#f1f1f1)}
.testimonial-label{position:absolute;left:0;width:1200px;top:3059px;text-align:center;font-family:"Old Standard TT",Georgia,serif;font-size:20px;color:var(--muted)}
.testimonial-text{position:absolute;left:165px;top:3088px;width:870px;text-align:center;font-size:14.6px;line-height:24.8px;color:var(--muted);font-weight:300}

/* blog */
.blog{position:absolute;left:0;top:3293px;width:1200px;height:1200px;background:var(--lilac-bg)}
.post{position:absolute;left:112px;width:976px;height:289px;background:var(--white)}
.post-image{position:absolute;left:24px;top:22px;width:316px;height:248px}
.post h3{position:absolute;left:366px;top:30px;font-family:"Old Standard TT",Georgia,serif;font-weight:700;font-size:20px;color:var(--ink)}
.post p{position:absolute;left:366px;width:480px;font-size:15.5px;line-height:27px;color:var(--muted);font-weight:300}

/* footer */
.site-footer{position:absolute;left:0;top:4493px;width:1200px;height:243px;background:var(--footer)}
.social{position:absolute;top:64px;width:22px;height:22px;border-radius:50%;background:var(--white)}
.footer-link{position:absolute;top:124px;font-family:"Old Standard TT",Georgia,serif;font-size:13px;color:var(--white);letter-spacing:1px}
.copyright{position:absolute;left:0;width:1200px;top:180px;text-align:center;font-family:"Montserrat",Arial,sans-serif;font-size:13px;color:#d8d8dc}
</style>
</head>
<body>

<header class="site-header">
  <div class="brand"><div class="brand-dot"></div><div class="brand-name">TQP<br>Medical</div></div>
  <nav class="nav">
    <a style="left:272px">HOME</a>
    <a style="left:351px">ABOUT US</a>
    <a style="left:456px">ULTRASOUND CLINICS</a>
    <a style="left:638px">COACHING AND COURSES</a>
    <a style="left:842px">FAQS</a>
  </nav>
  <div class="btn-book">BOOK NOW</div>
  <div class="btn-contact">CONTACT US</div>
</header>

<section class="hero" role="img" aria-label="Photo of two smiling women standing beside an ultrasound machine in a clinic room">
  <h1 class="hero-title">TQP MEDICAL</h1>
  <div class="btn-learn" style="left:114px;top:280px;width:176px">LEARN MORE
    <svg viewBox="0 0 16 16"><circle cx="8" cy="8" r="8" fill="#fff"/><path d="M6 4.5 9.5 8 6 11.5" stroke="#4d3790" stroke-width="2" fill="none"/></svg></div>
  <div class="play"><div class="play-dot"><svg width="16" height="16" viewBox="0 0 16 16"><path d="M4 2 14 8 4 14Z" fill="#23939b"/></svg></div>PLAY VIDEO</div>
</section>

<section class="clinics">
  <div class="clinic-ring"></div>
  <div class="clinic-ring-inner"></div>
  <div class="clinic-photo" role="img" aria-label="Photo of the two practitioners seated beside an ultrasound machine"></div>
  <h2 class="section-title abs" style="left:660px;top:832px">ULTRASOUND <span>CLINICS</span></h2>
  <div class="clinic-copy">
    <p>Lorem ipsum dolor sit amet, consectetur adipiscing elit, sed do eiusmod tempor incididunt ut labore et dolore magna aliqua. Ut enim ad minim veniam, quis nostrud exercitation ullamco laboris nisi ut aliquip ex ea commodo consequat.</p>
    <p>Duis aute irure dolor in reprehenderit in voluptate velit esse cillum dolore eu fugiat nulla pariatur. Excepteur sint occaecat cupidatat non proident, sunt in culpa qui officia deserunt laborum.</p>
  </div>
  <div class="btn-learn" style="left:660px;top:1136px;width:180px">LEARN MORE
    <svg viewBox="0 0 16 16"><circle cx="8" cy="8" r="8" fill="#fff"/><path d="M6 4.5 9.5 8 6 11.5" stroke="#4d3790" stroke-width="2" fill="none"/></svg></div>
</section>

<section class="coaching">
  <div class="coaching-photo" role="img" aria-label="Photo of a smiling woman with headphones writing notes at a laptop"></div>
  <div class="coaching-card">
    <h2>COACHING AND COURSES</h2>
    <p>Perspiciatis unde omnis iste natus error sit voluptatem accusalkseiios Intium doloremque laudantium, totam rem aperiam, eaawque ipsa quae ab illo inventore veritatis et quasi omnis iste natus error sit voluptatem accusantium doloremque laudantium, totam rem aperiam, eaque ipsa quae ab illo inventore veritatis et quasi architecto beatae visaerastae dicta sunt explicabo.</p>
    <div class="btn-learn" style="left:226px;top:333px;width:178px">LEARN MORE
      <svg viewBox="0 0 16 16"><circle cx="8" cy="8" r="8" fill="#fff"/><path d="M6 4.5 9.5 8 6 11.5" stroke="#4d3790" stroke-width="2" fill="none"/></svg></div>
  </div>
</section>

<section class="welcome">
  <h2 class="centered-title" style="top:94px">WELCOME VIDEO</h2>
  <div class="video">
    <div class="video-frame" role="img" aria-label="Video still of a 3D ultrasound image of a baby"></div>
    <div class="video-bar">
      <svg width="10" height="10" viewBox="0 0 10 10"><path d="M1 0 10 5 1 10Z" fill="#fff"/></svg>
      <span>0:00</span><div class="video-track"></div>
      <svg width="12" height="10" viewBox="0 0 12 10"><path d="M0 3h3l4-3v10L3 7H0Z" fill="#fff"/></svg>
      <svg width="11" height="11" viewBox="0 0 12 12"><circle cx="6" cy="6" r="4" stroke="#fff" stroke-width="2" fill="none"/></svg>
      <svg width="12" height="10" viewBox="0 0 12 10"><rect x="1" y="1" width="10" height="8" stroke="#fff" stroke-width="1.5" fill="none"/></svg>
    </div>
  </div>
</section>

<section class="testimonial">
  <h2 class="centered-title" style="top:2838px">TESTIMONIAL</h2>
  <div class="quote-mark">&ldquo;</div>
  <div class="avatar" role="img" aria-label="Circular portrait photo of a client"></div>
  <div class="testimonial-label">COACHING:</div>
  <p class="testimonial-text">"I knew I wanted to start my own business but I had no idea where to begin. It would have been easy to abort my dreams of starting my own business had it not been for the direction and unwavering support of Delphine from TQP medical. Delphine dissected the process into manageable bit sized pieces for me and worked tirelessly behind the scenes ensuring everything was on track. Her friendly, warm and approachable manner equated to more than her just being my business coach, she has now become a friend. Thank you!!"</p>
</section>

<section class="blog">
  <h2 class="centered-title" style="top:80px">BLOG</h2>

  <article class="post" style="top:158px">
    <div class="post-image" role="img" aria-label="Photo of a hand holding an ultrasound probe in front of a scanner" style="background:linear-gradient(135deg,#dfe6ee,#8fa3bb 50%,#e9ecef)"></div>
    <h3>DOLOR SIT AMET CONSECTETUR ADIPISCING</h3>
    <p style="top:64px">Lorem ipsum dolor sit amet,consectetur adipiscing elit.Lorem ipsum dolor sit amet,consectetur adipiscing elit.</p>
    <p style="top:128px">Orsit amet,consectetur adipiscing elit.Lorem ipsum dolor sit amet,consectetur adipiscing elit.</p>
    <div class="btn-learn" style="left:362px;top:204px;width:178px">LEARN MORE
      <svg viewBox="0 0 16 16"><circle cx="8" cy="8" r="8" fill="#fff"/><path d="M6 4.5 9.5 8 6 11.5" stroke="#4d3790" stroke-width="2" fill="none"/></svg></div>
  </article>

  <article class="post" style="top:491px">
    <div class="post-image" role="img" aria-label="Photo of a pregnant patient receiving an ultrasound scan" style="background:linear-gradient(135deg,#e9e2e6,#b9a4c4 45%,#a05566 80%)"></div>
    <h3>DOLOR SIT AMET CONSECTETUR ADIPISCING</h3>
    <p style="top:64px">Lorem ipsum dolor sit amet,consectetur adipiscing elit.Lorem ipsum dolor sit amet,consectetur adipiscing elit.</p>
    <p style="top:128px">Orsit amet,consectetur adipiscing elit.Lorem ipsum dolor sit amet,consectetur adipiscing elit.</p>
    <div class="btn-learn" style="left:362px;top:204px;width:178px">LEARN MORE
      <svg viewBox="0 0 16 16"><circle cx="8" cy="8" r="8" fill="#fff"/><path d="M6 4.5 9.5 8 6 11.5" stroke="#4d3790" stroke-width="2" fill="none"/></svg></div>
  </article>

  <article class="post" style="top:824px">
    <div class="post-image" role="img" aria-label="Photo of a patient lying on a bed during an ultrasound examination" style="background:linear-gradient(135deg,#d9a85f,#7b8fa6 45%,#d9cbb8 80%)"></div>
    <h3>DOLOR SIT AMET CONSECTETUR ADIPISCING</h3>
    <p style="top:64px">Lorem ipsum dolor sit amet,consectetur adipiscing elit.Lorem ipsum dolor sit amet,consectetur adipiscing elit.</p>
    <p style="top:128px">Orsit amet,consectetur adipiscing elit.Lorem ipsum dolor sit amet,consectetur adipiscing elit.</p>
    <div class="btn-learn" style="left:362px;top:204px;width:178px">LEARN MORE
      <svg viewBox="0 0 16 16"><circle cx="8" cy="8" r="8" fill="#fff"/><path d="M6 4.5 9.5 8 6 11.5" stroke="#4d3790" stroke-width="2" fill="none"/></svg></div>
  </article>
</section>

<footer class="site-footer">
  <div class="social" style="left:518px"></div>
  <div class="social" style="left:583px"></div>
  <div class="social" style="left:654px"></div>
  <span class="footer-link" style="left:447px">TERMS</span>
  <span class="footer-link" style="left:534px">PRIVACY</span>
  <span class="footer-link" style="left:635px">COOKIES POLICY</span>
  <p class="copyright">Copyright © 2022 | All Rights Reserved</p>
</footer>

</body>
</html>
```